Agriculture farming Hemp and CBD

The logo is in works with your company now, should be ready in a few days. We have our Domain (kestrelbrookhollow.com) We would like to see incorporated seed to growth, but not necessary. we would like to nature colors and some black and green. we have our farm and will be growing and selling HEMP and CBD we are based in the state of Virginia. Would like to incorporate the words pause, play, rewind if possible but not necessary.

Target Market(s)

20 years old to elderly

Coding

Coded - Design and coding required

Number of Pages Required

3 page

Font styles to use
Serif

Requirements
Must have
• I'm not sure on the must haves, we are open to any ideas, we would definitely like to see Hemp and CBD included, may the life cycle of seed to plant. We must have a pop up asking if you are 20 years old before they can enter our site and to view or purchase our product. I want the design to be totally different than what i uploaded.
Nice to have
• Would like to see natural colors as well as black and green
Should not have
• I want

```html
<!DOCTYPE html>
<html lang="en">
<head>
<meta charset="utf-8">
<title>Kestrel Brook Hollow – Home and Age Check</title>
<link rel="stylesheet" href="https://fonts.googleapis.com/css2?family=Poppins:ital,wght@0,500;0,600;0,700;1,400&family=Lato:ital,wght@0,400;0,700;1,400&display=swap">
<style>
:root{
  --green:#1db51d;
  --green-deep:#0f8a14;
  --ink:#111;
  --body:#6a6a6a;
  --board:#d9d9d9;
  --footer:#333;
  --white:#fff;
  --rule:#ececec;
}
*{box-sizing:border-box;margin:0;padding:0}
html,body{width:921px;height:1200px;overflow:hidden;background:var(--board)}
.canvas{width:921px;height:1200px;overflow:hidden;position:relative;background:var(--board)}
.board{position:absolute;left:0;top:0;width:1680px;height:2190px;transform:scale(.54821);transform-origin:0 0}
.page{position:absolute;top:131px;width:637px;height:1927px;background:var(--white);overflow:hidden;font-family:"Lato",sans-serif;color:var(--body)}
.page--home{left:145px}
.page--gated{left:898px}
.page > *{position:absolute}

/* header */
.site-header{left:0;top:0;width:637px;height:43px;background:var(--white)}
.brand{position:absolute;left:60px;top:11px;font-family:"Poppins",sans-serif;font-weight:600;font-size:14px;color:var(--ink);letter-spacing:-.2px}
.nav{position:absolute;left:262px;top:13px;display:flex;list-style:none;gap:0}
.nav li{font-size:7.5px;font-weight:700;color:var(--ink);text-transform:uppercase;height:17px;line-height:17px;margin-right:16px}
.nav li.is-active{background:var(--green);color:var(--white);padding:0 10px;margin-right:12px}

/* hero */
.hero{left:0;top:43px;width:637px;height:297px;background:
  radial-gradient(ellipse 160px 110px at 210px 40px,rgba(255,214,90,.95),rgba(220,170,40,.5) 45%,transparent 75%),
  linear-gradient(180deg,#6b6a1d 0%,#4d5a17 35%,#2e4a12 65%,#1d3a0d 100%)}
.hero__title{left:0;top:118px;width:637px;text-align:center;font-family:"Poppins",sans-serif;font-weight:700;font-size:35px;color:var(--white)}
.hero__text{left:100px;top:179px;width:437px;text-align:center;font-size:8px;line-height:16px;color:var(--white)}
.btn{display:block;border-radius:14px;background:var(--green);color:var(--white);font-size:7.5px;font-weight:700;text-transform:uppercase;text-align:center;line-height:26px;height:26px}
.btn i{display:inline-block;width:7px;height:7px;border-radius:50%;background:var(--white);margin-left:5px;vertical-align:-1px}
.hero__cta{left:273px;top:229px;width:90px}
.hero__dots{left:603px;top:165px;width:6px}
.hero__dots span{display:block;width:5px;height:5px;border-radius:50%;background:var(--white);margin-bottom:6.5px}
.hero__dots span.is-open{background:transparent;border:1px solid var(--white)}

/* shared headings */
.heading{font-family:"Poppins",sans-serif;font-weight:600;font-size:19px;color:var(--ink)}
.heading--center{left:0;width:637px;text-align:center}
.rule{height:2px;width:18px;background:var(--green)}
.copy{font-size:8px;line-height:14.2px;color:var(--body)}

/* about */
.about__title{left:58px;top:380px}
.about__rule{left:58px;top:410px}
.about__intro{left:58px;top:423px;width:226px}
.about__body{left:58px;top:459px;width:226px;text-align:justify}
.about__cta{left:58px;top:558px;width:84px}
.photo{border:3px solid var(--white);box-shadow:0 1px 4px rgba(0,0,0,.18)}
.about__photo-back{left:380px;top:385px;width:198px;height:145px;background:linear-gradient(135deg,#1d3d22,#3e6b3a 50%,#20402a)}
.about__photo-front{left:329px;top:439px;width:181px;height:147px;background:linear-gradient(160deg,#8ec25a,#4f8a2c 45%,#7a4a16 70%,#3f6a22)}
.section-rule{left:0;top:634px;width:637px;height:1px;background:var(--rule)}

/* types */
.types__title{top:664px}
.types__rule{left:309px;top:694px}
.types__item{top:720px;width:126px;height:121px}
.types__item--1{left:57px;background:linear-gradient(160deg,#4f8a2c,#2c5a1c 60%,#c8b24a)}
.types__item--2{left:190px;background:linear-gradient(160deg,#6a5532,#c7a23a 45%,#5a4630)}
.types__item--3{left:322px;background:linear-gradient(160deg,#6a7c2c,#b8b83a 45%,#4f6a24)}
.types__item--4{left:454px;background:linear-gradient(160deg,#b6b0a2,#6c6a4c 45%,#d9d6cf)}
.types__cta{left:277px;top:864px;width:84px}

/* why */
.why{left:0;top:937px;width:637px;height:205px;background:linear-gradient(90deg,#2e9a2e,#3fae35 40%,#6cc24e 70%,#88d06a)}
.why__title{top:961px;color:var(--white)}
.why__rule{left:309px;top:992px;background:var(--white)}
.why__text{left:60px;top:1010px;width:517px;text-align:center;font-size:7.5px;line-height:16.6px;color:var(--white)}
.why__play{left:298px;top:1071px;width:40px;height:40px;border-radius:50%;background:rgba(255,255,255,.35)}
.why__play::after{content:"";position:absolute;left:8px;top:8px;width:24px;height:24px;border-radius:50%;background:var(--white)}
.why__play svg{position:absolute;left:15px;top:14px;z-index:1}

/* testimonial */
.quote{left:0;top:1142px;width:637px;height:242px;background:linear-gradient(90deg,#fbfbfb,#f4f6f1 60%,#fbfaf5)}
.quote__backing{left:75px;top:1221px;width:145px;height:143px;border-radius:10px;background:#bfe7b8}
.quote__photo{left:83px;top:1211px;width:145px;height:143px;border-radius:10px;overflow:hidden;background:linear-gradient(160deg,#6e7f8a,#9aa7ad 50%,#4b5a62)}
.quote__name{left:83px;top:1315px;width:145px;height:39px;border-radius:0 0 10px 10px;background:var(--green);color:var(--white);text-align:center;font-family:"Lato",sans-serif;padding-top:6px}
.quote__name b{display:block;font-size:11px;line-height:12px}
.quote__name span{display:block;font-size:9px;line-height:12px}
.quote__mark{left:72px;top:1183px;font-family:"Poppins",sans-serif;font-weight:700;font-size:52px;line-height:52px;color:var(--green)}
.quote__title{left:279px;top:1208px}
.quote__rule{left:279px;top:1240px}
.quote__text{left:279px;top:1254px;width:287px;font-style:italic;font-size:7.3px;line-height:16.7px;text-align:justify;color:var(--body)}
.quote__dots{left:279px;top:1331px;display:flex;gap:2px}
.quote__dots span{width:6px;height:6px;border-radius:50%;background:var(--green)}
.quote__dots span.is-open{background:var(--white);border:1px solid var(--green)}

/* blog */
.blog__title{top:1400px}
.blog__rule{left:309px;top:1430px}
.card{top:1460px;width:169px;height:211px;background:var(--white);box-shadow:0 1px 4px rgba(0,0,0,.15)}
.card--1{left:59px}.card--2{left:234px}.card--3{left:408px}
.card__media{position:absolute;left:2px;top:1px;width:165px;height:106px}
.card--1 .card__media{background:linear-gradient(120deg,#a58a55,#5d7a2a 50%,#2e3f22)}
.card--2 .card__media{background:linear-gradient(180deg,#b8cfe0,#5d8a2e 40%,#3e6a1e)}
.card--3 .card__media{background:linear-gradient(120deg,#dfe9d6,#7aa24a 50%,#3e6a1e)}
.card__title{position:absolute;left:9px;top:119px;width:150px;font-size:7.2px;line-height:14px;font-weight:700;color:#333;text-transform:uppercase}
.card__meta{position:absolute;left:9px;top:153px;font-size:7px;color:#555;display:flex;align-items:center;gap:4px;white-space:nowrap}
.card__meta svg{flex:none}
.card__meta em{font-style:normal;margin-right:5px}
.card__text{position:absolute;left:9px;top:171px;width:150px;font-size:7px;line-height:14px;color:var(--body)}

/* footer */
.footer{left:0;top:1722px;width:637px;height:205px;background:var(--footer)}
.contact{top:1757px;width:120px;text-align:center;color:var(--white)}
.contact__icon{width:33px;height:33px;border-radius:50%;background:var(--white);margin:0 auto 8px;display:flex;align-items:center;justify-content:center}
.contact__label{font-size:7.5px;font-weight:700;text-decoration:underline;text-transform:uppercase;line-height:10px}
.contact__value{font-size:7.5px;line-height:14px;margin-top:4px}
.contact--1{left:56px}.contact--2{left:200px}.contact--3{left:343px}.contact--4{left:488px}
.footer__rule{left:58px;top:1844px;width:520px;height:1px;background:#555}
.footer__nav{left:58px;top:1861px;display:flex;list-style:none}
.footer__nav li{font-size:7.5px;color:var(--white);text-transform:uppercase;margin-right:18px}
.social{top:1857px;width:19px;height:19px;border-radius:50%;background:var(--green)}
.social--1{left:477px}.social--2{left:503px}.social--3{left:530px}.social--4{left:556px}
.footer__copy{left:0;top:1894px;width:637px;text-align:center;font-size:7.5px;color:var(--white)}

/* age check */
.veil{left:0;top:0;width:637px;height:1927px;background:rgba(20,20,20,.52)}
.age-check{left:135px;top:118px;width:367px;height:222px;background:var(--white);border:5px solid var(--green);text-align:center}
.age-check__brand{margin-top:29px;font-family:"Poppins",sans-serif;font-weight:600;font-size:13px;color:var(--ink)}
.age-check__title{margin-top:20px;font-family:"Poppins",sans-serif;font-weight:600;font-size:14px;color:var(--ink)}
.age-check__text{margin:14px auto 0;width:290px;font-size:7.3px;line-height:14.5px;color:var(--body)}
.age-check__actions{display:flex;justify-content:center;gap:14px;margin-top:13px}
.age-check__actions .btn{width:88px;height:27px;line-height:27px}
.btn--dark{background:#050505;width:68px!important}
</style>
</head>
<body>
<div class="canvas">
<div class="board">

<!-- HOME PAGE -->
<div class="page page--home">
  <header class="site-header">
    <div class="brand">kestrelbrookhollow.com</div>
    <ul class="nav"><li class="is-active">Home</li><li>About Us</li><li>Hemp</li><li>Reviews</li><li>Latest Blog</li><li>Contact Us</li></ul>
  </header>
  <div class="hero" role="img" aria-label="Sunlit hemp field at dawn with forest behind"></div>
  <h1 class="hero__title">Pause , Play , Rewind</h1>
  <p class="hero__text">Lorem ipsum dolor sit amet, consectetur adipiscing elit, sed do eiusmod tempor incididunt ut labore et dolore magna aliqua. Ut enim ad minim veniam, quis nostrud exercitation ullamco</p>
  <a class="btn hero__cta">Get Started<i></i></a>
  <div class="hero__dots"><span></span><span></span><span class="is-open"></span><span></span><span></span></div>

  <h2 class="heading about__title">About Us</h2>
  <div class="rule about__rule"></div>
  <p class="copy about__intro">Lorem ipsum dolor sit amet, consectetur adipiscing elit, sed do eiusmod tempor incididunt</p>
  <p class="copy about__body">Lorem ipsum dolor sit amet, consectetur adipiscing elit, sed do eiusmod tempor incididunt ut labore et dolore magna aliqua. Ut enim ad minim veniam, quis nostrud exercitation ullamco laboris nisi ut aliquip ex ea commodo consequat. Lorem ipsum dolor sit amet, consectetur adipiscing elit</p>
  <a class="btn about__cta">View More<i></i></a>
  <div class="photo about__photo-back" role="img" aria-label="Hemp leaves in deep green shade"></div>
  <div class="photo about__photo-front" role="img" aria-label="Dropper over an amber CBD oil bottle among hemp leaves"></div>
  <div class="section-rule"></div>

  <h2 class="heading heading--center types__title">Types Of Hemps</h2>
  <div class="rule types__rule"></div>
  <div class="photo types__item types__item--1" role="img" aria-label="Gloved hand holding CBD oil vial by a hemp plant"></div>
  <div class="photo types__item types__item--2" role="img" aria-label="Hemp oil jar with seeds on a wooden table"></div>
  <div class="photo types__item types__item--3" role="img" aria-label="Glass of hemp oil with seeds and leaf"></div>
  <div class="photo types__item types__item--4" role="img" aria-label="Small CBD bottles beside hemp leaves"></div>
  <a class="btn types__cta">View More<i></i></a>

  <div class="why" role="img" aria-label="Green blurred hemp leaves and CBD bottle"></div>
  <h2 class="heading heading--center why__title">Why Choose Us</h2>
  <div class="rule why__rule"></div>
  <p class="why__text">Sed ut perspiciatis unde omnis iste natus error sit voluptatem accusantium doloremque laudantium,<br>totam rem aperiam, eaque ipsa quae ab illo inventore veritatis et quasi architecto beatae vitae dicta sunt explicabo.<br>Nemo enim ipsam voluptatem quia voluptas sit aspernatur aut odit aut fugit, sed quia conse</p>
  <div class="why__play"><svg width="10" height="12" viewBox="0 0 10 12"><path d="M1 1l8 5-8 5z" fill="#1db51d"/></svg></div>

  <div class="quote" role="img" aria-label="Faint hemp leaf background"></div>
  <div class="quote__backing"></div>
  <div class="quote__photo" role="img" aria-label="Portrait of a smiling customer"></div>
  <div class="quote__name"><b>ELLSWORTH</b><span>Businessman</span></div>
  <div class="quote__mark">”</div>
  <h2 class="heading quote__title">What Our Client Says</h2>
  <div class="rule quote__rule"></div>
  <p class="quote__text">Lorem ipsum dolor sit amet, consectetur adipiscing elit, sed do eiusmod tempor incididunt ut labore et dolore magna aliqua. Ut enim ad minim veniam, quis nostrud exercitation ullamco laboris nisi ut aliquip ex ea commodo consequat. Duis aute irure dolor in reprehenderit in voluptate.</p>
  <div class="quote__dots"><span></span><span></span><span class="is-open"></span><span></span><span></span></div>

  <h2 class="heading heading--center blog__title">Latest Blog</h2>
  <div class="rule blog__rule"></div>
  <article class="card card--1"><div class="card__media" role="img" aria-label="Grower inspecting hemp leaves"></div><h3 class="card__title">Lorem ipsum dolor sit amet, consectetur adipiscing.</h3><div class="card__meta"><svg width="7" height="7"><rect x=".5" y="1" width="6" height="5.5" fill="none" stroke="#1db51d"/></svg><em>01 Sep 2020</em><svg width="8" height="7"><ellipse cx="4" cy="3" rx="3.5" ry="2.5" fill="none" stroke="#1db51d"/></svg><em>2,254</em><svg width="7" height="7"><circle cx="3.5" cy="2" r="1.7" fill="none" stroke="#1db51d"/><path d="M.5 7a3 3 0 0 1 6 0" fill="none" stroke="#1db51d"/></svg><em>Ellsworth</em></div><p class="card__text">Sed ut perspiciatis unde omnis iste natus error sit voluptatem accusantium.</p></article>
  <article class="card card--2"><div class="card__media" role="img" aria-label="Scientist sampling hemp in a field"></div><h3 class="card__title">Lorem ipsum dolor sit amet, consectetur adipiscing.</h3><div class="card__meta"><svg width="7" height="7"><rect x=".5" y="1" width="6" height="5.5" fill="none" stroke="#1db51d"/></svg><em>01 Sep 2020</em><svg width="8" height="7"><ellipse cx="4" cy="3" rx="3.5" ry="2.5" fill="none" stroke="#1db51d"/></svg><em>2,254</em><svg width="7" height="7"><circle cx="3.5" cy="2" r="1.7" fill="none" stroke="#1db51d"/><path d="M.5 7a3 3 0 0 1 6 0" fill="none" stroke="#1db51d"/></svg><em>Ellsworth</em></div><p class="card__text">Sed ut perspiciatis unde omnis iste natus error sit voluptatem accusantium.</p></article>
  <article class="card card--3"><div class="card__media" role="img" aria-label="Researchers checking hemp plants"></div><h3 class="card__title">Lorem ipsum dolor sit amet, consectetur adipiscing.</h3><div class="card__meta"><svg width="7" height="7"><rect x=".5" y="1" width="6" height="5.5" fill="none" stroke="#1db51d"/></svg><em>01 Sep 2020</em><svg width="8" height="7"><ellipse cx="4" cy="3" rx="3.5" ry="2.5" fill="none" stroke="#1db51d"/></svg><em>2,254</em><svg width="7" height="7"><circle cx="3.5" cy="2" r="1.7" fill="none" stroke="#1db51d"/><path d="M.5 7a3 3 0 0 1 6 0" fill="none" stroke="#1db51d"/></svg><em>Ellsworth</em></div><p class="card__text">Sed ut perspiciatis unde omnis iste natus error sit voluptatem accusantium.</p></article>

  <footer class="footer"></footer>
  <div class="contact contact--1"><div class="contact__icon"><svg width="14" height="16" viewBox="0 0 14 16"><path d="M7 15S1.5 9 1.5 6a5.5 5.5 0 0 1 11 0C12.5 9 7 15 7 15z" fill="none" stroke="#1db51d" stroke-width="1.5"/><circle cx="7" cy="6" r="2" fill="#1db51d"/></svg></div><div class="contact__label">Address</div><div class="contact__value">Level 26, Lorem ipsum dolor<br>United States</div></div>
  <div class="contact contact--2"><div class="contact__icon"><svg width="16" height="12" viewBox="0 0 16 12"><rect x="1" y="1" width="14" height="10" fill="none" stroke="#1db51d" stroke-width="1.4"/><path d="M1 1l7 6 7-6" fill="none" stroke="#1db51d" stroke-width="1.4"/></svg></div><div class="contact__label">Email</div><div class="contact__value">info@companyname.com</div></div>
  <div class="contact contact--3"><div class="contact__icon"><svg width="14" height="14" viewBox="0 0 14 14"><path d="M3 1l2.5 3-1.5 2a8 8 0 0 0 4 4l2-1.5 3 2.5-2 2C6 13 1 8 1 3z" fill="#1db51d"/></svg></div><div class="contact__label">Phone Number</div><div class="contact__value">1 888 888 888</div></div>
  <div class="contact contact--4"><div class="contact__icon"><svg width="15" height="14" viewBox="0 0 15 14"><rect x="1" y="5" width="13" height="8" fill="none" stroke="#1db51d" stroke-width="1.3"/><rect x="4" y="1" width="7" height="4" fill="none" stroke="#1db51d" stroke-width="1.3"/><rect x="4" y="8" width="7" height="2" fill="#1db51d"/></svg></div><div class="contact__label">Fax</div><div class="contact__value">1 777 777 777</div></div>
  <div class="footer__rule"></div>
  <ul class="footer__nav"><li>Home</li><li>About Us</li><li>Hemp</li><li>Reviews</li><li>Latest Blog</li><li>Contact Us</li></ul>
  <span class="social social--1"></span><span class="social social--2"></span><span class="social social--3"></span><span class="social social--4"></span>
  <p class="footer__copy">© 2020 Kestrel Brook Hollow. All Rights Reserved</p>
</div>

<!-- HOME PAGE WITH AGE CHECK -->
<div class="page page--gated">
  <header class="site-header">
    <div class="brand">kestrelbrookhollow.com</div>
    <ul class="nav"><li class="is-active">Home</li><li>About Us</li><li>Hemp</li><li>Reviews</li><li>Latest Blog</li><li>Contact Us</li></ul>
  </header>
  <div class="hero" role="img" aria-label="Sunlit hemp field at dawn with forest behind"></div>
  <h1 class="hero__title">Pause , Play , Rewind</h1>
  <p class="hero__text">Lorem ipsum dolor sit amet, consectetur adipiscing elit, sed do eiusmod tempor incididunt ut labore et dolore magna aliqua. Ut enim ad minim veniam, quis nostrud exercitation ullamco</p>
  <a class="btn hero__cta">Get Started<i></i></a>
  <div class="hero__dots"><span></span><span></span><span class="is-open"></span><span></span><span></span></div>

  <h2 class="heading about__title">About Us</h2>
  <div class="rule about__rule"></div>
  <p class="copy about__intro">Lorem ipsum dolor sit amet, consectetur adipiscing elit, sed do eiusmod tempor incididunt</p>
  <p class="copy about__body">Lorem ipsum dolor sit amet, consectetur adipiscing elit, sed do eiusmod tempor incididunt ut labore et dolore magna aliqua. Ut enim ad minim veniam, quis nostrud exercitation ullamco laboris nisi ut aliquip ex ea commodo consequat. Lorem ipsum dolor sit amet, consectetur adipiscing elit</p>
  <a class="btn about__cta">View More<i></i></a>
  <div class="photo about__photo-back" role="img" aria-label="Hemp leaves in deep green shade"></div>
  <div class="photo about__photo-front" role="img" aria-label="Dropper over an amber CBD oil bottle among hemp leaves"></div>
  <div class="section-rule"></div>

  <h2 class="heading heading--center types__title">Types Of Hemps</h2>
  <div class="rule types__rule"></div>
  <div class="photo types__item types__item--1" role="img" aria-label="Gloved hand holding CBD oil vial by a hemp plant"></div>
  <div class="photo types__item types__item--2" role="img" aria-label="Hemp oil jar with seeds on a wooden table"></div>
  <div class="photo types__item types__item--3" role="img" aria-label="Glass of hemp oil with seeds and leaf"></div>
  <div class="photo types__item types__item--4" role="img" aria-label="Small CBD bottles beside hemp leaves"></div>
  <a class="btn types__cta">View More<i></i></a>

  <div class="why" role="img" aria-label="Green blurred hemp leaves and CBD bottle"></div>
  <h2 class="heading heading--center why__title">Why Choose Us</h2>
  <div class="rule why__rule"></div>
  <p class="why__text">Sed ut perspiciatis unde omnis iste natus error sit voluptatem accusantium doloremque laudantium,<br>totam rem aperiam, eaque ipsa quae ab illo inventore veritatis et quasi architecto beatae vitae dicta sunt explicabo.<br>Nemo enim ipsam voluptatem quia voluptas sit aspernatur aut odit aut fugit, sed quia conse</p>
  <div class="why__play"><svg width="10" height="12" viewBox="0 0 10 12"><path d="M1 1l8 5-8 5z" fill="#1db51d"/></svg></div>

  <div class="quote" role="img" aria-label="Faint hemp leaf background"></div>
  <div class="quote__backing"></div>
  <div class="quote__photo" role="img" aria-label="Portrait of a smiling customer"></div>
  <div class="quote__name"><b>ELLSWORTH</b><span>Businessman</span></div>
  <div class="quote__mark">”</div>
  <h2 class="heading quote__title">What Our Client Says</h2>
  <div class="rule quote__rule"></div>
  <p class="quote__text">Lorem ipsum dolor sit amet, consectetur adipiscing elit, sed do eiusmod tempor incididunt ut labore et dolore magna aliqua. Ut enim ad minim veniam, quis nostrud exercitation ullamco laboris nisi ut aliquip ex ea commodo consequat. Duis aute irure dolor in reprehenderit in voluptate.</p>
  <div class="quote__dots"><span></span><span></span><span class="is-open"></span><span></span><span></span></div>

  <h2 class="heading heading--center blog__title">Latest Blog</h2>
  <div class="rule blog__rule"></div>
  <article class="card card--1"><div class="card__media" role="img" aria-label="Grower inspecting hemp leaves"></div><h3 class="card__title">Lorem ipsum dolor sit amet, consectetur adipiscing.</h3><div class="card__meta"><svg width="7" height="7"><rect x=".5" y="1" width="6" height="5.5" fill="none" stroke="#1db51d"/></svg><em>01 Sep 2020</em><svg width="8" height="7"><ellipse cx="4" cy="3" rx="3.5" ry="2.5" fill="none" stroke="#1db51d"/></svg><em>2,254</em><svg width="7" height="7"><circle cx="3.5" cy="2" r="1.7" fill="none" stroke="#1db51d"/><path d="M.5 7a3 3 0 0 1 6 0" fill="none" stroke="#1db51d"/></svg><em>Ellsworth</em></div><p class="card__text">Sed ut perspiciatis unde omnis iste natus error sit voluptatem accusantium.</p></article>
  <article class="card card--2"><div class="card__media" role="img" aria-label="Scientist sampling hemp in a field"></div><h3 class="card__title">Lorem ipsum dolor sit amet, consectetur adipiscing.</h3><div class="card__meta"><svg width="7" height="7"><rect x=".5" y="1" width="6" height="5.5" fill="none" stroke="#1db51d"/></svg><em>01 Sep 2020</em><svg width="8" height="7"><ellipse cx="4" cy="3" rx="3.5" ry="2.5" fill="none" stroke="#1db51d"/></svg><em>2,254</em><svg width="7" height="7"><circle cx="3.5" cy="2" r="1.7" fill="none" stroke="#1db51d"/><path d="M.5 7a3 3 0 0 1 6 0" fill="none" stroke="#1db51d"/></svg><em>Ellsworth</em></div><p class="card__text">Sed ut perspiciatis unde omnis iste natus error sit voluptatem accusantium.</p></article>
  <article class="card card--3"><div class="card__media" role="img" aria-label="Researchers checking hemp plants"></div><h3 class="card__title">Lorem ipsum dolor sit amet, consectetur adipiscing.</h3><div class="card__meta"><svg width="7" height="7"><rect x=".5" y="1" width="6" height="5.5" fill="none" stroke="#1db51d"/></svg><em>01 Sep 2020</em><svg width="8" height="7"><ellipse cx="4" cy="3" rx="3.5" ry="2.5" fill="none" stroke="#1db51d"/></svg><em>2,254</em><svg width="7" height="7"><circle cx="3.5" cy="2" r="1.7" fill="none" stroke="#1db51d"/><path d="M.5 7a3 3 0 0 1 6 0" fill="none" stroke="#1db51d"/></svg><em>Ellsworth</em></div><p class="card__text">Sed ut perspiciatis unde omnis iste natus error sit voluptatem accusantium.</p></article>

  <footer class="footer"></footer>
  <div class="contact contact--1"><div class="contact__icon"><svg width="14" height="16" viewBox="0 0 14 16"><path d="M7 15S1.5 9 1.5 6a5.5 5.5 0 0 1 11 0C12.5 9 7 15 7 15z" fill="none" stroke="#1db51d" stroke-width="1.5"/><circle cx="7" cy="6" r="2" fill="#1db51d"/></svg></div><div class="contact__label">Address</div><div class="contact__value">Level 26, Lorem ipsum dolor<br>United States</div></div>
  <div class="contact contact--2"><div class="contact__icon"><svg width="16" height="12" viewBox="0 0 16 12"><rect x="1" y="1" width="14" height="10" fill="none" stroke="#1db51d" stroke-width="1.4"/><path d="M1 1l7 6 7-6" fill="none" stroke="#1db51d" stroke-width="1.4"/></svg></div><div class="contact__label">Email</div><div class="contact__value">info@companyname.com</div></div>
  <div class="contact contact--3"><div class="contact__icon"><svg width="14" height="14" viewBox="0 0 14 14"><path d="M3 1l2.5 3-1.5 2a8 8 0 0 0 4 4l2-1.5 3 2.5-2 2C6 13 1 8 1 3z" fill="#1db51d"/></svg></div><div class="contact__label">Phone Number</div><div class="contact__value">1 888 888 888</div></div>
  <div class="contact contact--4"><div class="contact__icon"><svg width="15" height="14" viewBox="0 0 15 14"><rect x="1" y="5" width="13" height="8" fill="none" stroke="#1db51d" stroke-width="1.3"/><rect x="4" y="1" width="7" height="4" fill="none" stroke="#1db51d" stroke-width="1.3"/><rect x="4" y="8" width="7" height="2" fill="#1db51d"/></svg></div><div class="contact__label">Fax</div><div class="contact__value">1 777 777 777</div></div>
  <div class="footer__rule"></div>
  <ul class="footer__nav"><li>Home</li><li>About Us</li><li>Hemp</li><li>Reviews</li><li>Latest Blog</li><li>Contact Us</li></ul>
  <span class="social social--1"></span><span class="social social--2"></span><span class="social social--3"></span><span class="social social--4"></span>
  <p class="footer__copy">© 2020 Kestrel Brook Hollow. All Rights Reserved</p>

  <div class="veil"></div>
  <div class="age-check" role="dialog" aria-label="Age check">
    <div class="age-check__brand">kestrelbrookhollow.com</div>
    <h2 class="age-check__title">ARE YOU OVER 20 YEARS OF AGE ?</h2>
    <p class="age-check__text">Lorem ipsum dolor sit amet, consectetur adipiscing elit, sed do eiusmod tempor incididunt ut labore et dolore magna aliqua. Ut enim ad minim veniam, quis nostrud exercitation ullamco laboris nisi ut aliquip ex ea commodo consequat.</p>
    <div class="age-check__actions"><a class="btn">I ’M OVER 20<i></i></a><a class="btn btn--dark">Exit<i></i></a></div>
  </div>
</div>

</div>
</div>
</body>
</html>
```